New template needed for Joomla 3.2 website

We are a mortgage origination company based in Johannesburg, South Africa and require a sleek, modern & professional look for our website.
The website is complete and your template should accommodate all pages on the site (there are not many) and be ready for Joomla implementation.
Our website can be viewed at www.keystonebondhub.co.za
Target Market(s)
We are targeting consumers who require mortgage finance to buy real estate. There is no particular demographic, except that we cater to South African home buyers exclusively!
Requirements
Must have
- It must look professional and modern.
Take a look at competitor websites:
www.ziva.co.za
www.pkbondfinder.com
http://www.tallwavegroup.co.za/bondpeak/
http://www.ridgeloan.co.za/
We want to beat the competition !!
Nice to have
- Website should blend with company logo and play on the symbol in the logo.
I want more of a people / photo element to the template. It needs to make us seem "tangible"

```html
<!DOCTYPE html>
<html lang="en">
<head>
<meta charset="utf-8">
<title>Keystone Bond Hub</title>
<link href="https://fonts.googleapis.com/css2?family=Fira+Sans:wght@300;400;500&family=Fira+Sans+Condensed:wght@400;500&family=Raleway:wght@500;800&display=swap" rel="stylesheet">
<style>
:root{
  --brand-blue:#0d6fae;
  --brand-deep:#0a4f86;
  --sky-top:#b9d3e6;
  --city-mid:#3f5a72;
  --city-dark:#1a2430;
  --panel:#f7f8f9;
  --text:#2b2f33;
  --muted:#9a9ea2;
  --link:#2aa3e0;
  --white:#ffffff;
}
*{box-sizing:border-box;margin:0;padding:0}
html,body{width:1003px;height:1200px;overflow:hidden}
body{position:relative;font-family:"Fira Sans",sans-serif;color:var(--text);background:var(--city-dark)}
.backdrop{position:absolute;inset:0;background:linear-gradient(180deg,var(--sky-top) 0%,#9bb7cc 10%,var(--city-mid) 30%,#2b3a4a 60%,var(--city-dark) 100%)}
.brand{position:absolute;left:88px;top:48px;display:flex;align-items:center;gap:10px}
.brand-mark{width:44px;height:44px;border-radius:50%;background:var(--brand-blue)}
.brand-name{font-size:26px;font-weight:500;color:var(--brand-deep);line-height:1}
.header-call{position:absolute;right:88px;top:53px;font-size:17px;color:var(--city-dark)}
.sidebar{position:absolute;left:91px;top:113px;width:238px;height:1047px;background:rgba(20,29,39,.82)}
.main-nav{position:absolute;left:21px;top:21px;list-style:none}
.main-nav li{height:30px;font-size:13.5px;color:var(--white)}
.main-nav li.current{color:var(--link)}
.faq-title{position:absolute;left:21px;top:254px;font-size:16px;font-weight:400;color:var(--white)}
.faq-item{position:absolute;left:21px;width:201px;height:130px;background:var(--white)}
.faq-item h3{height:29px;line-height:29px;padding-left:9px;font-size:12px;font-weight:400;color:var(--white);background:linear-gradient(180deg,#2a8fcf,var(--brand-deep))}
.faq-item p{padding:9px 9px 0;font-size:10px;line-height:15px;font-weight:300;color:#6f7479}
.social{position:absolute;left:22px;top:824px;display:flex;gap:7px}
.social span{width:18px;height:18px;border-radius:50%;background:#d5d8db}
.rule{position:absolute;left:0;width:238px;border-top:2px dotted #8a96a3}
.contact-title{position:absolute;left:22px;top:894px;font-size:20px;font-weight:400;color:var(--white)}
.contact-phone{position:absolute;left:20px;top:932px;font-size:14px;color:var(--white)}
.contact-mail{position:absolute;left:20px;top:957px;font-size:12px;color:var(--link)}
.copyright{position:absolute;left:10px;top:1012px;font-size:10.5px;color:var(--white)}
.content{position:absolute;left:347px;top:113px;width:588px;height:1047px;background:rgba(247,248,249,.93)}
.hero{position:absolute;left:19px;top:18px;width:551px;height:196px;background:linear-gradient(100deg,#cfdbe4 0%,#e8eef2 45%,#b8c8d6 75%,#8fa6ba 100%)}
.hero-tagline{position:absolute;left:22px;top:154px;padding:1px 3px;background:rgba(255,255,255,.85);font-family:"Raleway",sans-serif;font-weight:500;font-size:18px;color:var(--brand-deep)}
.hero-tagline b{font-weight:800}
.intro{position:absolute;left:22px;top:236px;width:540px;font-size:12.5px;line-height:20px;color:var(--text)}
.section-title{position:absolute;font-family:"Fira Sans Condensed",sans-serif;font-size:20px;font-weight:400;color:var(--brand-deep);white-space:nowrap}
.why-lead{position:absolute;left:22px;top:388px;font-size:11.5px;font-weight:300;color:var(--text)}
.feature{position:absolute;width:250px;padding-left:28px}
.feature::before{content:"";position:absolute;left:0;top:2px;width:18px;height:18px;border-radius:50%;background:var(--brand-blue)}
.feature h4{font-size:12.5px;font-weight:400;color:var(--text);line-height:15px}
.feature p{font-size:10.5px;line-height:15px;font-weight:300;color:var(--muted)}
.promo{position:absolute;width:255px;font-size:10.3px;line-height:15px;color:var(--muted);font-weight:300}
.btn{position:absolute;height:29px;line-height:29px;padding:0 11px;font-size:14px;font-weight:300;color:var(--white);background:linear-gradient(180deg,#1b86c6,var(--brand-deep));border-radius:2px}
.calc-title{position:absolute;left:22px;top:822px;font-size:19px;font-weight:500;color:#3d4348}
.calc-rule{position:absolute;left:20px;top:845px;width:492px;border-top:1px dashed #b5b9bd}
.calc-row{position:absolute;left:22px;width:480px;height:22px}
.calc-row label{position:absolute;left:0;top:4px;font-size:10px;font-weight:500;color:#4a5056}
.track{position:absolute;left:114px;top:9px;width:201px;height:4px;border-radius:2px;background:#6d7378}
.knob{position:absolute;top:-7px;width:18px;height:18px;border-radius:50%;background:radial-gradient(circle at 40% 35%,#3aa8c6,#0c4d74)}
.value{position:absolute;left:327px;top:0;width:143px;height:22px;border:1px solid #9ea3a7;border-radius:11px;background:var(--white);text-align:center;line-height:20px;font-size:11px;font-weight:500;color:#4a5056}
</style>
</head>
<body>
<div class="backdrop" role="img" aria-label="Evening city skyline with lit office towers and snowy trees"></div>

<header class="site-header">
  <div class="brand"><span class="brand-mark"></span><span class="brand-name">Keystone Bond Hub</span></div>
  <div class="header-call">Call : (010) 447 3812</div>
</header>

<aside class="sidebar">
  <ul class="main-nav">
    <li class="current">Home</li>
    <li>About Us</li>
    <li>Important Information</li>
    <li>Homeloan Calculators</li>
    <li>Apply On-Line</li>
    <li>Contact Us</li>
  </ul>
  <h2 class="faq-title">Frequently Ask Questions</h2>
  <div class="faq-item" style="top:293px"><h3>Lorem Ipsum Dolor Sit</h3><p>Lorem ipsum dolor sit amet, consectetuer adipiscing elit, sed diam nonummy nibh euismod tincidunt ut laoreet dolore magna aliquam erat volutpat.</p></div>
  <div class="faq-item" style="top:426px"><h3>Lorem Ipsum Dolor Sit</h3><p>Lorem ipsum dolor sit amet, consectetuer adipiscing elit, sed diam nonummy nibh euismod tincidunt ut laoreet dolore magna aliquam erat volutpat.</p></div>
  <div class="faq-item" style="top:559px"><h3>Lorem Ipsum Dolor Sit</h3><p>Lorem ipsum dolor sit amet, consectetuer adipiscing elit, sed diam nonummy nibh euismod tincidunt ut laoreet dolore magna aliquam erat volutpat.</p></div>
  <div class="social"><span></span><span></span><span></span><span></span><span></span></div>
  <div class="rule" style="top:875px"></div>
  <h2 class="contact-title">Contact Us</h2>
  <div class="contact-phone">(010) 447 3812</div>
  <div class="contact-mail">hello@keystonebondhub.co.za</div>
  <div class="rule" style="top:992px"></div>
  <div class="copyright">© Keystone Bond Hub. All rights reserved.</div>
</aside>

<main class="content">
  <div class="hero" role="img" aria-label="Smiling consultant in an office with colleagues in the background">
    <div class="hero-tagline"><b>FAST</b> Home <b>LOANS</b> Great Service</div>
  </div>
  <p class="intro">orem Ipsum is simply dummy text of the printing and typesetting industry. Lorem Ipsum has been the industry's standard dummy text ever since the 1500s, when an unknown printer took a galley of type and scrambled it to make a type specimen book. It has survived not only five centuries, but also the leap into electronic</p>

  <h2 class="section-title" style="left:22px;top:352px">Why Keystone Bond Hub?</h2>
  <p class="why-lead">Lorem ipsum dolor sit amet, consectetuer adipiscing elit, sed diam nonummy nibh euismod.</p>

  <div class="feature" style="left:22px;top:448px"><h4>100% Free of Charge</h4><p>Lorem ipsum dolor sit amet, consectetuer adipiscing elit, sed diam nonummy nibh</p></div>
  <div class="feature" style="left:325px;top:448px"><h4>Dedicated Customer Support</h4><p>Lorem ipsum dolor sit amet, consectetuer adipiscing elit, sed diam nonummy nibh</p></div>
  <div class="feature" style="left:22px;top:531px"><h4>Credit Help</h4><p>Lorem ipsum dolor sit amet, consectetuer adipiscing elit, sed diam nonummy nibh</p></div>
  <div class="feature" style="left:325px;top:531px"><h4>Exceptional Service</h4><p>Lorem ipsum dolor sit amet, consectetuer adipiscing elit, sed diam nonummy nibh</p></div>

  <h2 class="section-title" style="left:22px;top:631px">Keystone Lead Referral Program</h2>
  <p class="promo" style="left:22px;top:668px">We invite members of the public, estate agents, attorneys, property developers and all other property professionals to refer leads to us. Why not join our referral program and earn money for every successful lead. It pays!</p>
  <span class="btn" style="left:22px;top:761px">Join Today</span>

  <h2 class="section-title" style="left:313px;top:631px">Keystone Rewards Card</h2>
  <p class="promo" style="left:313px;top:668px">All members of our lead referal program will receive a Keystone Bond Hub rewards card. We will load money earned from referals to your card and for you to spend in any way you please! These rewards cards are accepted in all retail stores and restaurants.</p>
  <span class="btn" style="left:313px;top:761px">Apply Now</span>

  <h2 class="calc-title">Calculate</h2>
  <div class="calc-rule"></div>
  <div class="calc-row" style="top:857px"><label>My mortgage amount</label><div class="track"><span class="knob" style="left:25px"></span></div><div class="value">120.000 TL</div></div>
  <div class="calc-row" style="top:888px"><label>My loan term</label><div class="track"><span class="knob" style="left:90px"></span></div><div class="value">120 (Months)</div></div>
  <div class="calc-row" style="top:919px"><label>My installment amount</label><div class="track"><span class="knob" style="left:28px"></span></div><div class="value">1.697 TL/Months</div></div>
  <span class="btn" style="left:22px;top:970px">Apply Now</span>
</main>
</body>
</html>
```